"Inkvale" printing shop

-The design must be based around the attached HPID (home page information design) called "Inkvale - HPID".

The table boxes are just for approximate placement of information – you DON'T have to box everything in and you can arrange these. All fonts used in the HPID are only examples - you can use any Google font you wish.

- Information only is in orange text. Copy to go on the design in black text. Some instructions are in the HPID. Please be creative!

-The design needs to be modern. Colours are to be consistent with their new logo or complement it. Keep it clean and simple, you don't need to use lots of colours. Use lots of white.

- images / icons for the site need to be relevant and high quality, but they must also be free images or icons. I have attached a few examples that could be used.

Width of content will be 1100 pixels when implemented as a web page. Header height (without nav bar) 150-200 pixels.

If your design is chosen the winning PSD file will have to be provided as follows…
1. Canvas size of 2000px x 2000px - 72ppi in Adobe Photoshop (CS5 compatible)
2. Width of content section is 1100px wide - centered in the canvas
3. Any button rollovers/hovers in the PSD as hidden layers.
4. All fonts used must be Google fonts.
5. You will need to supply the chosen home page plus one example page (example page as a style guide for how all other pages will look). Example page is only the header and navigational bar at the top, an empty sector in the middle with a column (190 px wide) which can be left or right aligned which means the main sector is 910 pixels wide, and then the footer at the bottom of the page

Checklist - http://pagebuildertally.example/

Examples of some websites that have great design... don't copy them please but they are similar in look to what we are after....
http://www.rookfenly.example/

Industry/Entity Type

Printing

Font styles to use
Serif
Sans Serif

Requirements
Should not have
• Drop shadows, comic sans font

```html
<!DOCTYPE html>
<html lang="en">
<head>
<meta charset="utf-8">
<title>Inkvale – Printing &amp; Photocopying</title>
<link href="https://fonts.googleapis.com/css2?family=Oswald:wght@300;400;700&family=Ubuntu:wght@400;500&display=swap" rel="stylesheet">
<style>
:root{
  --navy:#383d98;
  --navy-dark:#2f3389;
  --pink:#c5406a;
  --ink:#333;
  --muted:#555;
  --line:#e4e4e4;
  --red:#e02a25;
  --magenta:#d4177e;
  --orchid:#c24fa8;
  --sky:#1e93d3;
  --green:#2e7d43;
  --indigo:#3b45a6;
  --footer:#3a3f9b;
  --bottom:#1b1b28;
}
*{box-sizing:border-box;margin:0;padding:0}
html,body{width:710px;height:1200px;overflow:hidden;background:#fff}
body{position:relative;font-family:"Ubuntu",sans-serif;color:var(--ink)}
.abs{position:absolute}

.topline{left:0;top:0;width:710px;height:2px;background:var(--navy)}
.header{left:0;top:2px;width:710px;height:83px;background:linear-gradient(#fff,#f7f8fa)}
.brand{left:58px;top:20px;display:flex;align-items:center;gap:8px}
.brand-dot{width:44px;height:44px;border-radius:50%;background:var(--navy)}
.brand-name{font:500 28px "Ubuntu",sans-serif;color:var(--navy)}
.tagline{left:300px;top:25px;width:170px}
.tagline h4{font:500 8px "Ubuntu",sans-serif;color:var(--navy);letter-spacing:.2px}
.tagline p{font-size:7px;line-height:12px;color:var(--muted);margin-top:6px}
.vsep{left:468px;top:22px;width:1px;height:40px;background:var(--line)}
.phone-ico{left:485px;top:31px;width:28px;height:28px;border-radius:50%;border:1px solid #ddd;background:#fff;display:flex;align-items:center;justify-content:center}
.contact-top{left:520px;top:31px}
.contact-top b{display:block;font:400 10.5px "Ubuntu",sans-serif;color:var(--navy)}
.contact-top span{font-size:6.5px;color:var(--muted)}

.nav{left:0;top:85px;width:710px;height:35px;border-top:1px solid var(--line);border-bottom:1px solid var(--line);background:#fafafa;display:flex;align-items:center;padding-left:50px}
.nav a{font:300 8.5px "Oswald",sans-serif;color:#333;text-decoration:none;padding:0 8px;border-right:1px solid var(--line);line-height:12px}
.nav a:last-child{border:none}

.hero{left:0;top:120px;width:710px;height:288px;background:linear-gradient(90deg,#f2f2f4,#e9e9ec)}
.hero-art{left:320px;top:120px;width:390px;height:288px;background:linear-gradient(135deg,#c9ccd3 0%,#e9a23b 35%,#c7443f 60%,#8fb4d8 85%,#eef0f3 100%);opacity:.75}
.hero h1{left:66px;top:190px;font:700 40px "Oswald",sans-serif;letter-spacing:-.5px;color:var(--navy)}
.hero h1 em{font-style:normal;color:var(--pink)}
.hero-sub{left:67px;top:243px;width:200px;font-size:10px;line-height:16px;color:#444}
.btn{display:inline-block;background:var(--navy);color:#fff;font:400 9.5px "Ubuntu",sans-serif;padding:0 12px;height:25px;line-height:25px;border-bottom:2px solid var(--navy-dark)}
.hero .btn{left:67px;top:286px}
.arrow{width:20px;height:20px;border-radius:50%;background:rgba(120,120,120,.45);display:flex;align-items:center;justify-content:center}

.tile{width:183px;height:61px;color:#fff;display:flex}
.tile .icon{width:45px;height:61px;background:rgba(0,0,0,.12);display:flex;align-items:center;justify-content:center}
.tile .txt{padding:8px 0 0 12px}
.tile h3{font:300 13px "Oswald",sans-serif}
.tile p{font-size:6.5px;line-height:11px;margin-top:3px}

.service{width:290px;height:85px}
.service .pic{position:absolute;left:0;top:0;width:83px;height:84px}
.service .body{position:absolute;left:100px;top:0;width:190px}
.service h2{font:400 10.5px "Ubuntu",sans-serif;color:#222}
.service p{font-size:6.3px;line-height:12px;color:var(--muted);margin:5px 0 7px}
.service .btn{height:24px;line-height:24px;font-size:9.5px;padding:0 9px}

.footer{left:0;top:962px;width:710px;height:206px;background:var(--footer);color:#fff}
.footer h5{font:400 9.5px "Ubuntu",sans-serif;letter-spacing:.2px}
.field{position:absolute;border:1px solid rgba(255,255,255,.25);height:21px;font-size:7px;padding:6px 8px;color:#fff}
.send{left:58px;top:171px;background:#111;color:#fff;font:500 7.5px "Ubuntu",sans-serif;padding:8px 12px}
.c-label{font:400 8.5px "Ubuntu",sans-serif}
.c-val{font-size:7.5px;line-height:12px;margin-top:4px;opacity:.9}
.info-links a{display:block;font-size:6.5px;line-height:12.2px;color:#fff;text-decoration:none}
.bottom{left:0;top:1168px;width:710px;height:32px;background:var(--bottom);color:#9a9aa6;font-size:7px;text-align:center;line-height:32px}
</style>
</head>
<body>

<div class="abs topline"></div>
<header class="abs header"></header>
<div class="abs brand"><span class="brand-dot"></span><span class="brand-name">Inkvale</span></div>
<div class="abs tagline"><h4>DUPLICATION IS OUR VOCATION</h4><p>Professional photocopying - digital &amp; film processing, design and printing</p></div>
<div class="abs vsep"></div>
<div class="abs phone-ico"><svg width="12" height="12" viewBox="0 0 24 24"><path fill="#999" d="M6.6 10.8a15 15 0 0 0 6.6 6.6l2.2-2.2c.3-.3.7-.4 1-.2 1.1.4 2.3.6 3.6.6.6 0 1 .4 1 1V20c0 .6-.4 1-1 1A17 17 0 0 1 3 4c0-.6.4-1 1-1h3.5c.6 0 1 .4 1 1 0 1.3.2 2.5.6 3.6.1.3 0 .7-.2 1z"/></svg></div>
<div class="abs contact-top"><b>+1 07 555 0148</b><span>7/52 Harbour Lane - Kelmore - Westhaven</span></div>

<nav class="abs nav">
  <a>HOME</a><a>ABOUT</a><a>PHOTOCOPYIN</a><a>PRINTIN</a><a>LAMINATIN</a><a>BUSINESS CARD</a><a>TYPING SERVICE</a><a>FILM PROCESSIN</a><a>FREE QUOTE</a><a>PASSPORT PHOTOS</a><a>CONTACT</a>
</nav>

<section class="abs hero"></section>
<div class="abs hero-art" role="img" aria-label="Printer producing a spread of colourful photo prints"></div>
<h1 class="abs hero" style="background:none;width:auto;height:auto;left:66px;top:190px;font:700 40px 'Oswald',sans-serif;color:var(--navy)">Digital <em>Printing</em></h1>
<p class="abs hero-sub">laminating and photocopying services throughout Westhaven</p>
<a class="abs btn" style="left:67px;top:286px">More Information</a>
<div class="abs arrow" style="left:19px;top:231px"><svg width="8" height="8" viewBox="0 0 10 10"><path d="M7 1 3 5l4 4" stroke="#fff" stroke-width="1.5" fill="none"/></svg></div>
<div class="abs arrow" style="left:668px;top:231px"><svg width="8" height="8" viewBox="0 0 10 10"><path d="m3 1 4 4-4 4" stroke="#fff" stroke-width="1.5" fill="none"/></svg></div>

<!-- service tiles -->
<div class="abs tile" style="left:58px;top:428px;background:var(--red)"><div class="icon"><svg width="26" height="26" viewBox="0 0 24 24" fill="#fff"><rect x="3" y="11" width="18" height="9" rx="1"/><path d="M5 11 9 5h7l-2 6z"/></svg></div><div class="txt"><h3>Photocopying</h3><p>Lorem ipsum dolor sit amet,<br>consectetur adipiscing elit, sed</p></div></div>
<div class="abs tile" style="left:263px;top:428px;background:var(--magenta)"><div class="icon"><svg width="26" height="26" viewBox="0 0 24 24" fill="none" stroke="#fff" stroke-width="1.5"><rect x="3" y="5" width="18" height="15"/><path d="M6 10h12M6 13h12M6 16h12M5 3v4M9 3v4M13 3v4M17 3v4"/></svg></div><div class="txt"><h3>Laminating &amp; Binding</h3><p>Lorem ipsum dolor sit amet,<br>consectetur adipiscing elit, sed</p></div></div>
<div class="abs tile" style="left:468px;top:428px;background:var(--orchid)"><div class="icon"><svg width="26" height="26" viewBox="0 0 24 24" fill="#fff"><rect x="6" y="3" width="12" height="5"/><rect x="2" y="9" width="20" height="8" rx="1"/><rect x="6" y="15" width="12" height="6" fill="#fff" stroke="#c24fa8"/></svg></div><div class="txt"><h3>Digital Printing</h3><p>Lorem ipsum dolor sit amet,<br>consectetur adipiscing elit, sed</p></div></div>
<div class="abs tile" style="left:58px;top:510px;background:var(--sky)"><div class="icon"><svg width="26" height="26" viewBox="0 0 24 24" fill="none" stroke="#fff" stroke-width="2"><rect x="3" y="3" width="18" height="18"/><path d="M7 3v18M17 3v18M3 8h4M3 12h4M3 16h4M17 8h4M17 12h4M17 16h4"/></svg></div><div class="txt"><h3>Film Processing</h3><p>Lorem ipsum dolor sit amet,<br>consectetur adipiscing elit, sed</p></div></div>
<div class="abs tile" style="left:263px;top:510px;background:var(--green)"><div class="icon"><svg width="26" height="26" viewBox="0 0 24 24" fill="none" stroke="#fff" stroke-width="1.5"><rect x="3" y="8" width="18" height="13" rx="1"/><rect x="10" y="3" width="4" height="6"/><circle cx="8" cy="14" r="2"/><path d="M12 13h6M12 16h6M6 18h4"/></svg></div><div class="txt"><h3>Business Cards</h3><p>Lorem ipsum dolor sit amet,<br>consectetur adipiscing elit, sed</p></div></div>
<div class="abs tile" style="left:468px;top:510px;background:var(--indigo)"><div class="icon"><svg width="26" height="26" viewBox="0 0 24 24" fill="#fff"><path d="M3 7h4l2-3h6l2 3h4v13H3z"/><circle cx="12" cy="13" r="4.5" fill="#3b45a6"/><circle cx="12" cy="13" r="2.5"/></svg></div><div class="txt"><h3>Photo Printing</h3><p>Lorem ipsum dolor sit amet,<br>consectetur adipiscing elit, sed</p></div></div>

<!-- service highlights -->
<article class="abs service" style="left:58px;top:606px"><div class="pic" role="img" aria-label="Office worker at a photocopier" style="background:linear-gradient(135deg,#c7ccd6,#5d9fd0)"></div><div class="body"><h2>Cost Effective Photocopying</h2><p>No matter the quantity of photocopies you need or the size of your copy - you can rely on us to provide a top quality service</p><a class="btn">Click for Photocopying</a></div></article>
<article class="abs service" style="left:384px;top:606px"><div class="pic" role="img" aria-label="Person browsing photos on a tablet" style="background:linear-gradient(135deg,#6b6f78,#2f6fa3)"></div><div class="body"><h2>Personal desktop publishing</h2><p>From personalised brochures, posters and birthday and special occasion cards to top quality, cheap business cards - you get it all!</p><a class="btn">Click for Desktop Publishing</a></div></article>
<article class="abs service" style="left:58px;top:722px"><div class="pic" role="img" aria-label="Loupe resting on a colour calibration chart" style="background:linear-gradient(135deg,#e0457b,#f2c93a,#3aa3d8)"></div><div class="body"><h2>All digital format printing</h2><p>Either email us your file or bring it into the store and we can get you the print you need. All prints are to the highest quality.</p><a class="btn">Click for Digital Printing</a></div></article>
<article class="abs service" style="left:384px;top:722px"><div class="pic" role="img" aria-label="Collage of printed family photographs" style="background:linear-gradient(135deg,#c89a6f,#6e8fb3)"></div><div class="body"><h2>Film photo processing</h2><p>Bring in your film to the store and we will work with you to get the best quality print for your purpose and needs. We work with it al</p><a class="btn">Click for Photo Film Processing</a></div></article>
<article class="abs service" style="left:58px;top:839px"><div class="pic" role="img" aria-label="Close-up of a spiral-bound document" style="background:linear-gradient(180deg,#e8e8ea,#8a8a90 70%,#3048a8)"></div><div class="body"><h2>Laminating and binding</h2><p>Create a professional image for your documents or books. Lamination and binding also keeps your documents well protected</p><a class="btn">Click for Lamination &amp; Binding</a></div></article>
<article class="abs service" style="left:384px;top:839px"><div class="pic" role="img" aria-label="Photo prints flying out of a laptop" style="background:linear-gradient(135deg,#f3f4f6,#9bb3cc)"></div><div class="body"><h2>Quality digital photo print</h2><p>Get your photo printed to your requirements - either from a file or from your digital camera. With a wide range of options you can get the print you want</p><a class="btn">Digital Photo Printing</a></div></article>

<!-- footer -->
<footer class="abs footer">
  <h5 class="abs" style="left:57px;top:22px">GET A FREE QUOTE</h5>
  <div class="field" style="left:57px;top:45px;width:133px">Name</div>
  <div class="field" style="left:204px;top:45px;width:133px">Address</div>
  <div class="field" style="left:57px;top:75px;width:133px">Email</div>
  <div class="field" style="left:204px;top:75px;width:133px">Phone</div>
  <div class="field" style="left:57px;top:108px;width:278px;height:49px">Message</div>
  <div class="abs send">SEND MESSAGE</div>

  <h5 class="abs" style="left:383px;top:25px">CONTACT US</h5>
  <svg class="abs" style="left:381px;top:55px" width="10" height="11" viewBox="0 0 24 24"><path fill="#fff" d="M12 2a7 7 0 0 0-7 7c0 5 7 13 7 13s7-8 7-13a7 7 0 0 0-7-7zm0 9.5A2.5 2.5 0 1 1 12 6.5a2.5 2.5 0 0 1 0 5z"/></svg>
  <div class="abs" style="left:406px;top:55px"><div class="c-label">ADDRESS</div><div class="c-val">7/52 Harbour Lane - Kelmore -<br>Westhaven</div></div>
  <svg class="abs" style="left:381px;top:102px" width="10" height="10" viewBox="0 0 24 24"><path fill="#fff" d="M6.6 10.8a15 15 0 0 0 6.6 6.6l2.2-2.2c.3-.3.7-.4 1-.2 1.1.4 2.3.6 3.6.6.6 0 1 .4 1 1V20c0 .6-.4 1-1 1A17 17 0 0 1 3 4c0-.6.4-1 1-1h3.5c.6 0 1 .4 1 1 0 1.3.2 2.5.6 3.6.1.3 0 .7-.2 1z"/></svg>
  <div class="abs" style="left:406px;top:102px"><div class="c-label">CALL US</div><div class="c-val" style="margin-top:6px">07 555 0148,</div></div>
  <svg class="abs" style="left:381px;top:145px" width="12" height="10" viewBox="0 0 24 20"><rect x="1" y="1" width="22" height="18" fill="none" stroke="#fff" stroke-width="2"/><path d="m1 2 11 9 11-9" fill="none" stroke="#fff" stroke-width="2"/></svg>
  <div class="abs" style="left:406px;top:145px"><div class="c-label">E - MAIL</div><div class="c-val" style="margin-top:6px">hello@inkvale.example</div></div>

  <h5 class="abs" style="left:571px;top:25px">INFORMATION</h5>
  <div class="abs info-links" style="left:571px;top:52px"><a>HOME</a><a>ABOUT US</a><a>PHOTOCOPYING</a><a>PRINTING</a><a>LAMINATING</a><a>BUSINESS CARDS</a><a>TYPING SERVICES</a><a>FILM PROCESSING</a><a>PHOTO PRINTING</a></div>
</footer>
<div class="abs bottom">Copyright 2015 Inkvale. All rights reserved.</div>

</body>
</html>
```